Computer consultant business card

Bexil Software is a newly started computer consulting company. It's a small one-man company that provides mostly Vornix applications but also websites in collaboration with designers. I'm running this company on the side of full time university studies.

I want the final design to be clean and memorable. Be creative! :)

Some inspiration:
http://www.pixelmarta.com/design/48317
http://www.pixelmarta.com/design/2739164/business-card-design-by-frostlynk
http://www.pixelmarta.com/design/604281/business-card-design-by-koralind-vestrabanu

See attachment for my company logo.
Updates

I would like to thank everyone for submitting! I'll need a couple of days to review and ultimately select a design.

Target Market(s)

Non-technical entrepreneurs and small companies.

Industry/Entity Type

University

Requirements
Must have
• My company logo.
In any way, both colors from my logo.
First- and last name, e-mail and phone number.
Double-sided design.
Nice to have
• Something creative with the symbol in my logo

```html
<!DOCTYPE html>
<html lang="en">
<head>
<meta charset="utf-8">
<title>Bexil Software – Business Card</title>
<link rel="stylesheet" href="https://fonts.googleapis.com/css2?family=Source+Sans+3:wght@400;600&display=swap">
<style>
  :root {
    --stage: #e9e6e2;
    --card-blue: #4670b8;
    --card-glow: #b4c0e6;
    --tint: rgba(255, 255, 255, 0.22);
    --ink: #ffffff;
  }
  * { box-sizing: border-box; margin: 0; padding: 0; }
  html, body {
    width: 1200px;
    height: 789px;
    overflow: hidden;
    background: var(--stage);
    font-family: "Source Sans 3", "Myriad Pro", sans-serif;
    color: var(--ink);
  }
  .canvas {
    width: 1200px;
    height: 789px;
    display: flex;
    align-items: center;
    justify-content: center;
    gap: 80px;
  }
  .card {
    position: relative;
    width: 350px;
    height: 600px;
    background: var(--card-blue);
    overflow: hidden;
    box-shadow: 0 6px 18px rgba(0, 0, 0, 0.18);
  }
  /* back side */
  .card--back {
    background: radial-gradient(circle at 50% 45%, var(--card-glow) 0%, #8194d2 22%, var(--card-blue) 55%);
  }
  .back-mark {
    position: absolute;
    left: 50%;
    top: 45%;
    width: 110px;
    height: 110px;
    transform: translate(-50%, -50%);
    border-radius: 50%;
    border: 22px solid var(--card-blue);
  }
  .back-url {
    position: absolute;
    bottom: 30px;
    width: 100%;
    text-align: center;
    font-size: 15px;
    letter-spacing: 0.2px;
  }
  /* front side */
  .brand {
    position: absolute;
    top: 120px;
    width: 100%;
    display: flex;
    align-items: center;
    justify-content: center;
    gap: 14px;
  }
  .brand-dot {
    width: 44px;
    height: 44px;
    border-radius: 50%;
    background: var(--ink);
  }
  .brand-name {
    font-size: 52px;
    font-weight: 600;
    line-height: 1;
    letter-spacing: 1px;
  }
  .person {
    position: absolute;
    top: 290px;
    width: 100%;
    text-align: center;
  }
  .person-name { font-size: 16px; }
  .person-role { font-size: 13px; margin-top: 1px; }
  .front-arc {
    position: absolute;
    left: -70px;
    top: 340px;
    width: 490px;
    height: 490px;
  }
  .contact {
    position: absolute;
    bottom: 38px;
    width: 100%;
    text-align: center;
    font-size: 15px;
    line-height: 1.35;
  }
</style>
</head>
<body>
  <main class="canvas">
    <section class="card card--back" aria-label="Card back">
      <div class="back-mark"></div>
      <p class="back-url">www.yourdomain.com</p>
    </section>

    <section class="card card--front" aria-label="Card front">
      <svg class="front-arc" viewBox="0 0 490 490" aria-hidden="true">
        <circle cx="245" cy="245" r="245" fill="var(--tint)"/>
      </svg>
      <div class="brand">
        <span class="brand-dot"></span>
        <span class="brand-name">bexil</span>
      </div>
      <div class="person">
        <p class="person-name">Your Name Here</p>
        <p class="person-role">Designation</p>
      </div>
      <div class="contact">
        <p>Ph : 00-123-4567</p>
        <p>Fax : 00-123-4567</p>
        <p>name@yourdomain.com</p>
      </div>
    </section>
  </main>
</body>
</html>
```